IT Freelancer (Consulting, trainer and project manager) needed letterhead

As a freelancer for IT Trainingswhip, consulting and project management I need a letterhead design. What is desired is a design that fits the existing logo (see Annex). It is functional, reliable, and equal time wirkenn Agil and modern. The whole is in color, as well as printed out to make a good impression on a black and white printer. The whole is to the existing Cooperate design (business card, homepage, logo) fit. Therefore, the choice of colors.
Updates

Target Market(s)

Customers such as medium-sized enterprises, training institutions

Industry/Entity Type

Consulting

Colors
0455a3
3277b5
85abd2
cfdfed
34a6d7
32a6d6
249fd4
0792cd
85cae6

Requirements
Must have
• Must include logo (see Annex) address (Brunnerweg 14, 95617 Lindenfeld, Germany). Must seriously and act simultaneously Agil. Design should (even) be adaptable (signature, address, etc.) design must look good on a black / white laser

```html
<!DOCTYPE html>
<html lang="en">
<head>
<meta charset="utf-8">
<title>Lukas Brenner – Letterhead</title>
<link href="https://fonts.googleapis.com/css2?family=Montserrat:wght@400;500;700&display=swap" rel="stylesheet">
<style>
  :root {
    --brand-blue: #0455a3;
    --brand-cyan: #34a6d7;
    --brand-pale: #cfdfed;
    --ink: #1c1c1c;
    --paper: #ffffff;
    --backdrop: #e4e6ea;
  }
  * { box-sizing: border-box; margin: 0; padding: 0; }
  html, body { width: 1200px; height: 1000px; overflow: hidden; background: var(--backdrop); }
  body { font-family: "Montserrat", Arial, sans-serif; color: var(--ink); }
  .letterhead {
    position: absolute; left: 246px; top: 0; width: 707px; height: 1000px;
    background: var(--paper); overflow: hidden;
    box-shadow: 0 4px 18px rgba(0,0,0,.18);
  }
  .header-band { position: absolute; left: 0; top: 0; width: 707px; height: 200px; }
  .contact-list {
    position: absolute; right: 40px; top: 22px; list-style: none;
    color: var(--paper); font-size: 9.5px; line-height: 13px; font-weight: 500;
  }
  .contact-list li { display: flex; gap: 6px; align-items: flex-start; }
  .contact-list .icon { width: 9px; height: 9px; margin-top: 2px; flex: none; }
  .watermark {
    position: absolute; right: -90px; bottom: 190px; width: 330px; height: 330px;
    border-radius: 50%; background: var(--brand-pale); opacity: .55;
  }
  .brand { position: absolute; left: 50px; top: 230px; display: flex; align-items: center; gap: 10px; }
  .brand-dot { width: 46px; height: 46px; border-radius: 50%; background: var(--brand-blue); }
  .brand-name { font-weight: 700; font-size: 17px; line-height: 18px; color: var(--brand-blue); letter-spacing: 1px; text-transform: uppercase; }
  .recipient { position: absolute; left: 70px; top: 330px; font-size: 11px; line-height: 16px; font-style: normal; }
  .recipient strong { font-weight: 700; }
  .letter-body { position: absolute; left: 95px; top: 450px; width: 560px; font-size: 11px; line-height: 17px; }
  .salutation { font-weight: 700; margin-bottom: 22px; }
  .letter-body p { margin-bottom: 17px; }
  .closing { position: absolute; left: 95px; top: 790px; font-size: 11px; }
  .signature {
    position: absolute; left: 95px; top: 815px; width: 160px; height: 55px;
    background: linear-gradient(90deg, #f1f1f1, #e6e6e6); border-radius: 3px;
  }
  .signer { position: absolute; left: 95px; top: 880px; font-size: 11px; }
</style>
</head>
<body>
<main class="letterhead">
  <svg class="header-band" viewBox="0 0 707 200" aria-hidden="true">
    <path d="M180 0 H707 V140 Q450 210 180 0 Z" fill="var(--brand-cyan)"/>
    <path d="M190 0 H707 V122 Q450 195 190 0 Z" fill="var(--brand-blue)"/>
  </svg>

  <ul class="contact-list">
    <li><svg class="icon" viewBox="0 0 10 10"><rect width="10" height="10" rx="1.5" fill="#fff"/><path d="M3 2h2v6H3z" fill="var(--brand-blue)"/></svg>+49(0) 171 / 4 27 18 36</li>
    <li><svg class="icon" viewBox="0 0 10 10"><rect width="10" height="10" rx="1.5" fill="#fff"/><path d="M2.5 3h5v4h-5z" fill="var(--brand-blue)"/></svg>+49(0) 9471 / 7 40 21 58</li>
    <li><svg class="icon" viewBox="0 0 10 10"><rect width="10" height="10" rx="1.5" fill="#fff"/><path d="M2 4h6v3H2z" fill="var(--brand-blue)"/></svg>+49(0) 9471 / 62 14</li>
    <li><svg class="icon" viewBox="0 0 10 10"><rect width="10" height="10" rx="1.5" fill="#fff"/><path d="M2 3l3 2.5L8 3v4H2z" fill="var(--brand-blue)"/></svg>lukas.brenner@mail-box.de</li>
    <li><svg class="icon" viewBox="0 0 10 10"><rect width="10" height="10" rx="1.5" fill="#fff"/><path d="M5 2a2 2 0 0 1 2 2c0 1.5-2 4-2 4S3 5.5 3 4a2 2 0 0 1 2-2z" fill="var(--brand-blue)"/></svg><span>Brunnerweg 14<br>95617 Lindenfeld<br>Germany</span></li>
    <li><svg class="icon" viewBox="0 0 10 10"><rect width="10" height="10" rx="1.5" fill="#fff"/><circle cx="5" cy="5" r="2.5" fill="none" stroke="var(--brand-blue)"/></svg>www.brenner-it.de</li>
  </ul>

  <div class="watermark" aria-hidden="true"></div>

  <div class="brand">
    <div class="brand-dot" aria-hidden="true"></div>
    <div class="brand-name">Lukas<br>Brenner</div>
  </div>

  <address class="recipient">
    To<br>
    <strong>Lorem Ipsum is simply</strong><br>
    <strong>Lorem Ipsum</strong><br>
    Address Line 1 text of the printing and<br>
    Address Line 2 text
  </address>

  <section class="letter-body">
    <div class="salutation">Dear Alex,</div>
    <p>dummy text of the printing and typesetting industry. Lorem Ipsum has been the industry's standard dummy text ever since the 1500s, when an unknown printer took a galley of type and scrambled it to make a type specimen book. It has survived not only five centuries, but also the leap into electronic typesetting, remaining essentially unchanged.</p>
    <p>It is a long established fact that a reader will be distracted by the readable content of a page when looking at its layout. The point of using Lorem Ipsum is that it has a more-or-less normal distribution of letters, as opposed to using 'Content here, content here', making it look like readable English. Many desktop publishing packages and web page editors now.</p>
    <p>Contrary to popular belief, Lorem Ipsum is not simply random text. It has roots in a piece of classical Latin literature from 45 BC, making it over 2000 years old. Henry Caldwell, a Latin professor at Ashford Hill College in Virginia, looked up one of the more obscure Latin words, consectetur, from a Lorem Ipsum passage.</p>
  </section>

  <div class="closing">Lorem Ipsum</div>
  <div class="signature" role="img" aria-label="Handwritten signature"></div>
  <div class="signer">Lorem Ipsum is a dummy</div>
</main>
</body>
</html>
```